'Sorry we missed you'/ 'How did we do'

I need a 'sorry we missed you' card, and a 'how did we do' card. I have attached a reference for existing cards, and have provided our current logo, and our social media header (van photo).
For the 'How did we do' flyer, I would like for this to have a QR code of our quillorby account 'Corvane Mistline Fittings Ltd', which has 0 reviews at the moment.
If looking for any clarifications please message, the tone of the flyers should be professional.
Flyer will be vertical A6 format.
Edit- for clarity, I want 2x variations. One for ‘sorry we missed you’ and another for ‘How did we do’ each with descriptions above.

```html
<!DOCTYPE html>
<html lang="en">
<head>
<meta charset="UTF-8">
<title>Sorry We Missed You – Corvane Mistline Fittings Ltd</title>
<link rel="stylesheet" href="https://fonts.googleapis.com/css2?family=Poppins:wght@300;400;700&display=swap">
<style>
  :root {
    --blue-deep: #15508f;
    --blue-mid: #1f63ad;
    --blue-light: #2f74b8;
    --orange: #ff6b2c;
    --white: #ffffff;
  }
  * { margin: 0; padding: 0; box-sizing: border-box; }
  html, body { width: 850px; height: 1200px; overflow: hidden; background: var(--blue-deep); }
  .flyer {
    position: relative;
    width: 850px;
    height: 1200px;
    overflow: hidden;
    font-family: 'Poppins', sans-serif;
    color: var(--white);
    background: linear-gradient(160deg, var(--blue-mid) 0%, var(--blue-deep) 100%);
  }
  .backdrop, .url-ring { position: absolute; inset: 0; }
  .url-ring { pointer-events: none; }
  .url-ring text {
    font-family: 'Poppins', sans-serif;
    font-size: 22px;
    font-weight: 400;
    letter-spacing: 0.5px;
    fill: var(--white);
  }
  .headline {
    position: absolute;
    left: 68px;
    top: 62px;
    font-size: 86px;
    font-weight: 700;
    line-height: 1.02;
    letter-spacing: -0.5px;
  }
  .intro {
    position: absolute;
    left: 68px;
    top: 262px;
    font-size: 29px;
    font-weight: 300;
    line-height: 1.45;
  }
  .van-photo {
    position: absolute;
    left: 68px;
    top: 407px;
    width: 522px;
    height: 522px;
    border-radius: 50%;
    border: 5px solid var(--white);
    background: linear-gradient(180deg, #c9cdd0 0%, #9aa4ad 30%, #3b4b60 55%, #2b3a4e 80%, #8f9396 100%);
  }
  .call-to-action {
    position: absolute;
    left: 68px;
    top: 975px;
    font-size: 29px;
    font-weight: 700;
  }
  .brand-mark {
    position: absolute;
    left: 62px;
    top: 1040px;
    width: 120px;
    display: flex;
    flex-direction: column;
    align-items: flex-start;
    gap: 6px;
    font-size: 15px;
    font-weight: 700;
    line-height: 1.15;
  }
  .brand-mark .dot {
    width: 26px; height: 26px; border-radius: 50%;
    background: var(--orange);
  }
  .contact {
    position: absolute;
    left: 192px;
    top: 1036px;
    font-size: 25px;
    font-weight: 300;
    font-style: normal;
    line-height: 1.36;
  }
  .contact strong { font-weight: 700; }
</style>
</head>
<body>
<main class="flyer">
  <svg class="backdrop" width="850" height="1200" viewBox="0 0 850 1200" aria-hidden="true">
    <polygon points="560,0 850,0 850,430 300,1200 0,1200 0,980" fill="var(--blue-light)" opacity="0.35"/>
    <circle cx="362" cy="668" r="330" fill="var(--white)" opacity="0.07"/>
    <path d="M640,0 H850 V210 C850,260 810,285 760,275 C690,262 625,200 620,120 C616,60 625,20 640,0 Z" fill="var(--orange)"/>
    <line x1="832" y1="640" x2="702" y2="798" stroke="var(--white)" stroke-width="30" stroke-linecap="round"/>
  </svg>

  <h1 class="headline">Sorry We<br>Missed You</h1>
  <p class="intro">We attempted to perform fire<br>sprinkler maintenance at your Property today</p>

  <div class="van-photo" role="img" aria-label="Photo of the company service van parked outside a building"></div>

  <svg class="url-ring" width="850" height="1200" viewBox="0 0 850 1200">
    <defs>
      <path id="url-arc" d="M503.5,899.6 A290,290 0 0 0 614.6,617.6"/>
    </defs>
    <text><textPath href="#url-arc">www.corvanemistline.scot</textPath></text>
  </svg>

  <p class="call-to-action">Please contact us to arrange another visit</p>

  <div class="brand-mark">
    <span class="dot"></span>
    <span>Corvane Mistline</span>
  </div>

  <address class="contact">
    14 Harrow Quay, Edinburgh EH6 4RT<br>
    <strong>Tel:</strong> 0131 496 0382<br>
    <strong>Email:</strong> info@corvanemistline.scot
  </address>
</main>
</body>
</html>
```